Business card design for my company.
I would like the card's background colour to be black. You can also see our web site to get an idea of our brand. https://www.tmwhomecrafting.com.au/
- Name
- Email

```html
<!DOCTYPE html>
<html lang="en">
<head>
<meta charset="utf-8">
<title>TMW Home Crafting – Business Card</title>
<link rel="stylesheet" href="https://fonts.googleapis.com/css2?family=Montserrat:wght@300;400;600;700&display=swap">
<style>
  :root {
    --stage: #5a5a5a;
    --card: #222222;
    --card-back: #242424;
    --ink-faint: #191919;
    --green: #1d9a48;
    --white: #f2f2f2;
    --muted: #d6d6d6;
  }
  * { margin: 0; padding: 0; box-sizing: border-box; }
  html, body {
    width: 1200px; height: 875px; overflow: hidden;
    background: var(--stage);
    font-family: "Montserrat", sans-serif;
  }
  .canvas {
    width: 1200px; height: 875px;
    display: flex; flex-direction: column; align-items: center; justify-content: center;
    gap: 56px;
  }
  .card {
    width: 630px; height: 360px;
    border-radius: 22px;
    position: relative;
    overflow: hidden;
  }
  .card-back { background: var(--card-back); }
  .card-front { background: var(--card); }

  .back-brand {
    position: absolute; inset: 0;
    display: flex; align-items: center; justify-content: center;
    gap: 16px;
    font-weight: 700; font-size: 40px; letter-spacing: 3px;
    color: var(--ink-faint);
  }
  .back-brand .brand-square {
    width: 26px; height: 26px; background: var(--ink-faint);
  }

  .front-brand {
    position: absolute; top: 62px; right: 44px;
    display: flex; align-items: center; gap: 12px;
    font-weight: 700; font-size: 24px; letter-spacing: 2px;
    color: var(--white);
  }
  .front-brand .brand-square { width: 18px; height: 18px; background: var(--green); }

  .identity {
    position: absolute; top: 118px; left: 0;
    display: flex; align-items: stretch; gap: 18px;
  }
  .identity .accent-bar { width: 22px; background: var(--green); margin-top: 30px; height: 28px; }
  .identity .person-name {
    font-weight: 700; font-size: 27px; color: var(--green); letter-spacing: 1px;
  }
  .identity .person-title {
    font-weight: 300; font-size: 16px; color: var(--white); margin-top: 2px;
  }

  .contacts {
    position: absolute; left: 58px; bottom: 40px;
    list-style: none;
    font-weight: 400; font-size: 15px; color: var(--muted);
  }
  .contacts li { display: flex; align-items: center; gap: 10px; line-height: 28px; }
  .contacts svg { width: 13px; height: 13px; fill: var(--green); flex: none; }
</style>
</head>
<body>
<main class="canvas">
  <section class="card card-back" aria-label="Card back">
    <div class="back-brand"><span class="brand-square"></span>TMW HOME CRAFTING</div>
  </section>

  <section class="card card-front" aria-label="Card front">
    <div class="front-brand"><span class="brand-square"></span>TMW HOME CRAFTING</div>

    <div class="identity">
      <span class="accent-bar"></span>
      <div>
        <p class="person-name">DARREN HALE</p>
        <p class="person-title">CEO/Founder</p>
      </div>
    </div>

    <ul class="contacts">
      <li>
        <svg viewBox="0 0 24 24" aria-hidden="true"><path d="M6.6 10.8a15.1 15.1 0 0 0 6.6 6.6l2.2-2.2c.3-.3.7-.4 1-.2 1.1.4 2.3.6 3.6.6.6 0 1 .4 1 1V20c0 .6-.4 1-1 1A17 17 0 0 1 3 4c0-.6.4-1 1-1h3.5c.6 0 1 .4 1 1 0 1.3.2 2.5.6 3.6.1.3 0 .7-.2 1z"/></svg>
        897-555-0142
      </li>
      <li>
        <svg viewBox="0 0 24 24" aria-hidden="true"><path d="M2 5h20v14H2z M2 5l10 8 10-8" /></svg>
        info@tmwhomecrafting.com.au
      </li>
      <li>
        <svg viewBox="0 0 24 24" aria-hidden="true"><circle cx="12" cy="12" r="10"/></svg>
        www.tmwhomecrafting.com.au
      </li>
    </ul>
  </section>
</main>
</body>
</html>
```